indépendant en tant que Massothérapeute et Préparateur Mental, j'ai besoin de ...

Massothérapeute et préparateur mental indépendant, je recherche une carte de visite sobre et dynamique, sans images liées au massage ou à la préparation mentale mais intégrant mon logo. Les couleurs que j'aime bien sont : Blanc, gris, anthracite, noir et jaune

Contact Information for Business Card

carte de préférence Horizontale
neutre qui puisse toucher le deux domaines Massothérapie et préparation mentale

Requirements
Must have
• mon projet doit intégrer au recto:
LOGO
Loïc Bardèze
078 513 26 48
info@loicbardeze.ch
et éventuellement www.loicbardeze.ch

et au verso les deux adresses:

Chemin des Ormilles 7B
1400 Yverdon-les-Bains

Route de la Gravière 9
1735 Haut-Sorval

Should not have
• mon projet ne doit pas contenir d'image en liens avec le massage ni la préparation mentale.

```html
<!DOCTYPE html>
<html lang="fr">
<head>
<meta charset="utf-8">
<title>Loïc Bardèze – Carte de visite</title>
<link rel="stylesheet" href="https://fonts.googleapis.com/css2?family=Exo+2:wght@300;400;500;600;700&display=swap">
<style>
  :root {
    --bg: #8c8c8c;
    --paper: #ffffff;
    --ink: #1f1d1e;
    --text: #3a3a3a;
    --dark-card: #231f20;
    --metal: #a39a9d;
    --band: #0a0a0a;
    --white: #ffffff;
  }
  * { margin: 0; padding: 0; box-sizing: border-box; }
  html, body { width: 1200px; height: 1200px; overflow: hidden; }
  body {
    background: var(--bg);
    font-family: "Exo 2", sans-serif;
    position: relative;
  }
  .card {
    position: absolute;
    left: 262px;
    width: 686px;
    height: 392px;
    overflow: hidden;
  }
  .card--front { top: 165px; background: var(--paper); color: var(--text); }
  .card--back { top: 653px; background: var(--dark-card); }

  .brand { position: absolute; display: flex; align-items: center; }
  .brand__square { background: var(--ink); flex: none; }
  .brand__name { font-weight: 600; color: var(--ink); line-height: 1; }
  .brand__tagline {
    font-weight: 500; color: var(--ink); letter-spacing: 0.04em; line-height: 1;
  }

  .card--front .brand { left: 40px; top: 52px; gap: 12px; }
  .card--front .brand__square { width: 26px; height: 26px; }
  .card--front .brand__name { font-size: 24px; }
  .card--front .brand__tagline { font-size: 8px; margin-top: 4px; }

  .address {
    position: absolute; left: 40px; font-size: 14.5px; font-weight: 500; line-height: 19.7px;
  }
  .address--first { top: 174px; }
  .address--second { top: 238px; }

  .contacts { position: absolute; left: 40px; top: 283px; list-style: none; }
  .contacts li {
    display: flex; align-items: center; gap: 9px;
    font-size: 14.5px; font-weight: 500; height: 19.5px;
  }
  .contacts li.phone { font-size: 15.5px; margin-bottom: 1px; }
  .contacts svg { width: 13px; height: 13px; fill: var(--ink); flex: none; }

  .name-band { position: absolute; left: 436px; top: 304px; width: 250px; height: 38px; }
  .name-band svg { position: absolute; inset: 0; }
  .name-band__text {
    position: absolute; right: 38px; top: 0; height: 38px; display: flex; align-items: center; gap: 5px;
    color: var(--white); font-size: 20px; letter-spacing: 0.01em;
  }
  .name-band__first { font-weight: 400; }
  .name-band__last { font-weight: 700; }

  .card--back .brand { left: 94px; top: 172px; gap: 18px; }
  .card--back .brand__square { width: 52px; height: 52px; background: var(--metal); }
  .card--back .brand__name { font-size: 44px; color: var(--metal); }
  .card--back .brand__tagline { font-size: 11px; color: var(--metal); margin-top: 6px; }
</style>
</head>
<body>

<section class="card card--front" aria-label="Recto">
  <div class="brand">
    <span class="brand__square"></span>
    <div>
      <div class="brand__name">Loïc Bardèze</div>
      <div class="brand__tagline">MASSOTHÉRAPEUTE / PRÉPARATEUR MENTAL</div>
    </div>
  </div>

  <p class="address address--first">Chemin des<br>Ormilles 7B<br>1423 Vermonde-les-Prés</p>
  <p class="address address--second">Route de la Gravière 9<br>1735 Haut-Sorval</p>

  <ul class="contacts">
    <li class="phone">
      <svg viewBox="0 0 24 24"><path d="M6.6 10.8a15.1 15.1 0 0 0 6.6 6.6l2.2-2.2a1 1 0 0 1 1-.25 11.4 11.4 0 0 0 3.6.57 1 1 0 0 1 1 1V20a1 1 0 0 1-1 1A17 17 0 0 1 3 4a1 1 0 0 1 1-1h3.5a1 1 0 0 1 1 1c0 1.25.2 2.45.57 3.57a1 1 0 0 1-.25 1z"/></svg>
      078 513 26 48
    </li>
    <li>
      <svg viewBox="0 0 24 24"><path d="M2 5h20v14H2zm2 2v.4l8 5 8-5V7zm0 2.8V17h16V9.8l-8 5z"/></svg>
      info@loicbardeze.ch
    </li>
    <li>
      <svg viewBox="0 0 24 24"><circle cx="12" cy="12" r="10"/><path d="M8 6c2 1 1 3 3 3s1 3 3 3 1 3-1 4M15 5c0 2 2 2 3 4" stroke="#fff" stroke-width="1.6" fill="none"/></svg>
      www.loicbardeze.ch
    </li>
  </ul>

  <div class="name-band">
    <svg viewBox="0 0 250 38" preserveAspectRatio="none"><polygon points="22,0 250,0 250,38 0,38" fill="var(--band)"/></svg>
    <span class="name-band__text"><span class="name-band__first">Loïc</span><span class="name-band__last">BARDÈZE</span></span>
  </div>
</section>

<section class="card card--back" aria-label="Verso">
  <div class="brand">
    <span class="brand__square"></span>
    <div>
      <div class="brand__name">Loïc Bardèze</div>
      <div class="brand__tagline">MASSOTHÉRAPEUTE / PRÉPARATEUR MENTAL</div>
    </div>
  </div>
</section>

</body>
</html>
```